We need a web page design for a new company called "Brambel". We provide an innovative music sharing mobile application that allows music listeners to share their music without paying for a monthly subscription. We would like to incorporate the attached logo and color scheme. The final design should communicate music gifting and sharing.

Industry/Entity Type

It Company

```html
<!DOCTYPE html>
<html lang="en">
<head>
<meta charset="utf-8">
<title>Brambel – Share Your Songs</title>
<link href="https://fonts.googleapis.com/css2?family=Oswald:wght@300;400;500&family=Open+Sans:ital,wght@0,400;0,600;1,400&family=Anton&display=swap" rel="stylesheet">
<style>
:root{
  --green:#5fa80a;
  --green-light:#7cc41c;
  --orange:#f39c0b;
  --dark:#222;
  --ink:#333;
  --line:#d6d6d6;
  --page:#f3f3f3;
  --white:#fff;
}
*{box-sizing:border-box;margin:0;padding:0}
html,body{width:884px;height:1200px;overflow:hidden}
body{position:relative;background:var(--page);font-family:"Open Sans",sans-serif;color:var(--ink)}
.abs{position:absolute}

/* header */
.site-header{left:0;top:0;width:884px;height:67px;background:var(--green)}
.brand{left:85px;top:8px;display:flex;align-items:center;gap:8px}
.brand-dot{width:34px;height:34px;border-radius:50%;background:var(--white)}
.brand-name{font-weight:600;font-size:34px;line-height:36px;color:var(--white)}
.brand-tag{left:137px;top:47px;font-size:11px;letter-spacing:4px;color:#cfe8a8}
.top-btn{top:7px;height:18px;font-size:8px;line-height:18px;text-align:center;color:var(--white);font-weight:600}
.btn-share{left:624px;width:80px;background:#82c42a}
.btn-login{left:714px;width:39px;background:var(--orange)}
.btn-sign{left:760px;width:40px;background:#111}
.main-nav{top:41px;left:0;font-family:"Oswald",sans-serif;font-weight:300;font-size:12.5px;color:var(--white)}
.main-nav span{position:absolute;white-space:nowrap}
.nav-active{left:383px;top:64px;width:36px;height:3px;background:#2c4f06}

/* hero */
.hero{left:0;top:67px;width:884px;height:343px;background:linear-gradient(100deg,#e6e2dd 0%,#d8d1ca 30%,#cbbfb3 52%,#ddd6d0 70%,#b9b2ad 100%)}
.hero-kicker{left:96px;top:166px;font-family:"Anton",sans-serif;font-size:32px;color:var(--green-light);letter-spacing:.5px}
.hero-with{left:96px;top:200px;font-family:"Anton",sans-serif;font-size:56px;line-height:66px;color:#111}
.hero-box{left:203px;top:206px;width:174px;height:62px;background:var(--green);color:var(--white);font-weight:600;font-size:40px;line-height:62px;text-align:center}
.hero-enjoy{left:98px;top:262px;font-family:"Oswald",sans-serif;font-weight:400;font-size:31px;color:#111}
.arrow{top:214px;width:27px;height:40px;background:var(--green)}
.arrow svg{display:block}

/* featured track */
.album-art{left:85px;top:446px;width:149px;height:121px;background:radial-gradient(circle at 50% 55%,#9a3d12,#4a1906 55%,#150704)}
.track-title{left:261px;top:441px;font-family:"Oswald",sans-serif;font-size:17px;color:#333}
.track-by{left:261px;top:464px;font-size:9px;font-style:italic;color:#888}
.stars{color:var(--green);letter-spacing:1px}
.track-stars{left:261px;top:483px;font-size:12px}
.player{left:261px;top:511px;width:181px;height:23px;background:#555;display:flex;align-items:center;padding:0 8px;gap:6px}
.player-track{flex:1;height:6px;border-radius:3px;background:linear-gradient(90deg,var(--green-light) 82%,var(--white) 82%)}
.track-caption{left:261px;top:546px;font-size:8.5px;font-style:italic;color:#888}
.track-text{left:85px;top:573px;width:365px;font-size:9.8px;line-height:11.5px;color:#666}

/* track list */
.tracklist{left:485px;top:430px;width:315px;height:167px;background:var(--white);border:1px solid #e4e4e4}
.row{position:absolute;left:0;width:313px;height:26px;border-bottom:1px solid #ececec;font-size:8.5px;color:#555}
.row:last-child{border-bottom:none}
.row span{position:absolute;top:8px}
.row .name{left:13px}
.row .time{left:147px}
.row .rstars{left:188px;top:6px;font-size:10px}
.row .rstars em{font-style:normal;color:#999}
.buy{position:absolute;left:264px;top:5px;width:44px;height:15px;background:var(--orange);border-radius:2px;font-size:8px;font-weight:600;line-height:15px;text-align:center;color:#222}

/* section headings */
.sec-title{font-family:"Oswald",sans-serif;font-weight:400;font-size:17px;color:#555}
.sec-rule{height:1px;background:var(--line)}
.sec-rule b{display:block;width:110px;height:1px;background:var(--green)}

/* news */
.news-img{left:85px;width:121px;height:99px}
.news-title{left:218px;font-size:12.5px;color:var(--green);white-space:nowrap}
.news-text{left:218px;width:232px;font-size:9.3px;line-height:11.6px;color:#777}
.more{color:var(--orange)}
.news-sep{left:85px;width:354px;height:1px;background:#ddd}

/* countdown */
.countdown{left:485px;top:670px;width:315px;height:96px;background:var(--white);border:1px solid #e3e3e3}
.cd{top:674px;width:70px;height:87px;background:#222;color:var(--white);text-align:center;font-family:"Oswald",sans-serif}
.cd.active{background:var(--green)}
.cd .num{font-weight:500;font-size:44px;line-height:52px;margin-top:6px;letter-spacing:-1px}
.cd .lbl{font-weight:300;font-size:12px;line-height:18px}
.event-note{left:490px;top:784px;font-size:9.6px;color:#444}
.tickets{left:700px;top:779px;width:96px;height:21px;background:var(--orange);border-radius:2px;font-family:"Oswald",sans-serif;font-size:12px;line-height:21px;text-align:center;color:#222}

/* video */
.video{left:485px;top:864px;width:315px;height:162px;background:linear-gradient(180deg,#8f8f8f,#4a4a4a 60%,#9c3a22 88%,#b8472a)}
.play{left:630px;top:933px;width:24px;height:24px;border-radius:50%;background:var(--white)}
.video-cap{left:485px;top:961px;width:315px;text-align:center;font-family:"Oswald",sans-serif;font-size:11px;color:var(--white)}

/* footer */
.site-footer{left:0;top:1062px;width:884px;height:138px;background:var(--dark)}
.foot-title{left:0;top:1077px;width:884px;text-align:center;font-family:"Oswald",sans-serif;font-size:17px;color:var(--white)}
.social{top:1115px;width:14px;height:14px;border-radius:50%;background:#e8e8e8}
.foot-nav{top:1144px;left:0;width:884px;font-family:"Oswald",sans-serif;font-weight:300;font-size:8.5px;color:var(--green-light)}
.foot-nav span{position:absolute;white-space:nowrap}
.copy{left:0;top:1162px;width:884px;text-align:center;font-family:"Oswald",sans-serif;font-weight:300;font-size:8.5px;color:#ddd}
</style>
</head>
<body>

<header class="site-header abs">
  <div class="brand abs"><span class="brand-dot"></span><span class="brand-name">Brambel</span></div>
  <div class="brand-tag abs">own the music</div>
  <div class="top-btn btn-share abs">SHARE YOUR MUSIC</div>
  <div class="top-btn btn-login abs">LOGIN</div>
  <div class="top-btn btn-sign abs">SING IN</div>
  <nav class="main-nav abs">
    <span style="left:386px">HOME</span>
    <span style="left:443px">EVENTS</span>
    <span style="left:506px">ALBUMS</span>
    <span style="left:574px">GALLERY</span>
    <span style="left:642px">BLOG</span>
    <span style="left:699px">FEATURES</span>
    <span style="left:774px">SHOP</span>
  </nav>
</header>
<div class="nav-active abs"></div>

<section class="hero abs" role="img" aria-label="Blurred photo of a person relaxing on a sofa with headphones, a hand in front holding a phone that shows the app playing a song"></section>
<div class="hero-kicker abs">Share Your Songs</div>
<div class="hero-with abs">With</div>
<div class="hero-box abs">Brambel</div>
<div class="hero-enjoy abs">and then enjoy...</div>
<div class="arrow abs" style="left:16px"><svg width="27" height="40" viewBox="0 0 27 40"><path d="M17 10 L9 20 L17 30" fill="none" stroke="#fff" stroke-width="1.6"/></svg></div>
<div class="arrow abs" style="left:837px"><svg width="27" height="40" viewBox="0 0 27 40"><path d="M10 10 L18 20 L10 30" fill="none" stroke="#fff" stroke-width="1.6"/></svg></div>

<div class="album-art abs" role="img" aria-label="Album cover artwork with dark red star and band names"></div>
<div class="track-title abs">Live My Life</div>
<div class="track-by abs">By Jhon Doe</div>
<div class="track-stars stars abs">★★★★★</div>
<div class="player abs">
  <svg width="32" height="8" viewBox="0 0 32 8"><path d="M5 0L0 4 5 8ZM10 0L5 4 10 8Z" fill="#7cc41c"/><path d="M14 0h2.5v8H14ZM18 0h2.5v8H18Z" fill="#fff"/><path d="M23 0l4 4-4 4ZM27 0l4 4-4 4Z" fill="#7cc41c"/></svg>
  <div class="player-track"></div>
</div>
<div class="track-caption abs">Lorem Ipsum Dolor sit amet concisneind</div>
<p class="track-text abs">Lorem ipsum dolor sit amet, consectetuer adipiscing elit, sed diam nonummy ni vel eum iriure dolor in hendrerit in euismod Investigationes demonstraverunt lectores legere me lius quod ii legunt saepius. Claritas est etiam processus dynamicus, qui sequitur mutationem consuetudium lectquam</p>

<div class="tracklist abs">
  <div class="row" style="top:0"><span class="name">Missing You</span><span class="time">0:38</span><span class="rstars stars">★★★★<em>★</em></span><div class="buy">$20 Buy</div></div>
  <div class="row" style="top:27px"><span class="name">Midnight In Tokyo</span><span class="time">2:51</span><span class="rstars stars">★★★★<em>★</em></span><div class="buy">$10 Buy</div></div>
  <div class="row" style="top:54px"><span class="name">Walking On Horizon</span><span class="time">4:29</span><span class="rstars stars">★★★★<em>★</em></span><div class="buy">$60 Buy</div></div>
  <div class="row" style="top:81px"><span class="name">A Happy Carefree Day</span><span class="time">2:45</span><span class="rstars stars">★★★★★</span><div class="buy">$30 Buy</div></div>
  <div class="row" style="top:108px"><span class="name">Through the Clouds</span><span class="time">5:56</span><span class="rstars stars">★★★★★</span><div class="buy">$20 Buy</div></div>
  <div class="row" style="top:135px"><span class="name">Live My Life</span><span class="time">3:56</span><span class="rstars stars">★★★★★</span><div class="buy">$10 Buy</div></div>
</div>

<h2 class="sec-title abs" style="left:85px;top:629px">Latest News</h2>
<div class="sec-rule abs" style="left:85px;top:658px;width:354px"><b></b></div>

<div class="news-img abs" style="top:675px;background:linear-gradient(135deg,#3a2a24,#b8453a 55%,#d9b7a0)" role="img" aria-label="Photo of a singer performing at a microphone"></div>
<div class="news-title abs" style="top:671px">Typi non habent claritatemt</div>
<p class="news-text abs" style="top:697px">Lorem ipsum dolor sit amet, consectetur adipiscing elit. In tellus orci, semper et ornare dictum, varius ut tellus. In consectetur consectetur adipiscing elit. I<br><br>n tellus orci, semper et ornare dictum, varius ut tellus. ... <span class="more">Read More</span></p>
<div class="news-sep abs" style="top:782px"></div>

<div class="news-img abs" style="top:794px;background:linear-gradient(180deg,#c9c3bb,#6e6560 60%,#3a3532)" role="img" aria-label="Group photo of a rock band"></div>
<div class="news-title abs" style="top:789px">Duis autem vel eum iriure dolor in hend</div>
<p class="news-text abs" style="top:815px">Lorem ipsum dolor sit amet, consectetur adipiscing elit. In tellus orci, semper et ornare dictum, varius ut tellus. In consectetur consectetur adipiscing elit.<br><br><span class="more">Read More</span></p>
<div class="news-sep abs" style="top:909px"></div>

<div class="news-img abs" style="top:922px;background:radial-gradient(circle at 45% 40%,#f7e0a0,#d9772e 45%,#5a2a14)" role="img" aria-label="Photo of a band on a brightly lit concert stage"></div>
<div class="news-title abs" style="top:917px">Lorem ipsum dolor sit amet</div>
<p class="news-text abs" style="top:943px">Lorem ipsum dolor sit amet, consectetur adipiscing elit. In tellus orci, semper et ornare dictum, varius ut tellus. In consectetur consectetur adipiscing elit. I<br><br>n tellus orci, semper et orn. <span class="more">Read More</span></p>

<h2 class="sec-title abs" style="left:485px;top:629px">Upcoming Events</h2>
<div class="sec-rule abs" style="left:485px;top:658px;width:315px"><b></b></div>
<div class="countdown abs"></div>
<div class="cd abs" style="left:490px"><div class="num">03</div><div class="lbl">DAYS</div></div>
<div class="cd active abs" style="left:568px"><div class="num">23</div><div class="lbl">HOURS</div></div>
<div class="cd abs" style="left:646px"><div class="num">59</div><div class="lbl">MINUTES</div></div>
<div class="cd abs" style="left:725px"><div class="num">26</div><div class="lbl">SECS</div></div>
<div class="event-note abs">Nam liber tempor cum soluta nobis eleifend</div>
<div class="tickets abs">Buy Tickets Now</div>

<h2 class="sec-title abs" style="left:485px;top:820px">Featured Videos</h2>
<div class="sec-rule abs" style="left:485px;top:850px;width:315px"><b></b></div>
<div class="video abs" role="img" aria-label="Black and white video still of a four-piece band in a city street"></div>
<div class="play abs"><svg width="24" height="24" viewBox="0 0 24 24"><path d="M9.5 7 L17 12 L9.5 17Z" fill="#222"/></svg></div>
<div class="video-cap abs">Nam liber tempor cum soluta</div>

<footer class="site-footer abs"></footer>
<div class="foot-title abs">Connect With Brambel</div>
<div class="social abs" style="left:289px" aria-label="Social link"></div>
<div class="social abs" style="left:321px" aria-label="Social link"></div>
<div class="social abs" style="left:353px" aria-label="Social link"></div>
<div class="social abs" style="left:385px" aria-label="Social link"></div>
<div class="social abs" style="left:417px" aria-label="Social link"></div>
<div class="social abs" style="left:449px" aria-label="Social link"></div>
<div class="social abs" style="left:481px" aria-label="Social link"></div>
<div class="social abs" style="left:513px" aria-label="Social link"></div>
<div class="social abs" style="left:545px" aria-label="Social link"></div>
<div class="social abs" style="left:577px" aria-label="Social link"></div>
<nav class="foot-nav abs">
  <span style="left:294px">HOME</span>
  <span style="left:334px">EVENTS</span>
  <span style="left:379px">ALBUMS</span>
  <span style="left:429px">GALLERY</span>
  <span style="left:476px">BLOG</span>
  <span style="left:517px">FEATURES</span>
  <span style="left:571px">SHOP</span>
</nav>
<div class="copy abs">Copyright © 2014 Brambel All rights reserved.</div>

</body>
</html>
```